This book will apply the 12 Steps to gaming addiction, also known as video game addiction. The primary purpose of the book is to provide an effective solution for this new type of addiction. The solution is based on the rich and successful concepts of traditional twelve-step programs like RQ.

The title on the cover will be "Nine Doors Out of the Endless Level" and "by Peter Halvorn". A subtitle can be used if it works in your design of "A Practical Path Back from Compulsive Screen Play". Cover will be for a 6" x 9" book approximately 110 pages in length.

Some back cover text including some review quotes and an author bio are in the attached Word doc. There is also an author photo attached for for the back cover.

Requirements
Must have
• For the cover design it could be stylized, or an image, a partial image, or whatever. I am open to suggestions. Think about what would be noticed by a person searching for help with moderating their video game use, or by the parents or loved ones of problem gamers. Something contemporary and eye catching.

```html
<!DOCTYPE html>
<html lang="en">
<head>
<meta charset="utf-8">
<title>Nine Doors Out of the Endless Level – Back Cover</title>
<link rel="stylesheet" href="https://fonts.googleapis.com/css2?family=Silkscreen:wght@700&family=Oswald:wght@500&family=Barlow+Semi+Condensed:wght@300;400;500&display=swap">
<style>
  :root {
    --navy: #0b1180;
    --night: #02030f;
    --ink: #ffffff;
    --lavender: #c9d0ff;
    --flame: #ff3b24;
    --rule: #d7402f;
    --panel: rgba(0, 0, 0, 0.55);
  }
  * { margin: 0; padding: 0; box-sizing: border-box; }
  html, body { width: 800px; height: 1200px; overflow: hidden; }
  body {
    position: relative;
    background: linear-gradient(200deg, var(--navy) 0%, #070b55 40%, #03052a 75%, var(--night) 100%);
    color: var(--ink);
    font-family: "Barlow Semi Condensed", "Arial Narrow", sans-serif;
    font-weight: 300;
  }
  .masthead { position: absolute; top: 76px; left: 0; width: 800px; text-align: center; }
  .masthead__kicker {
    font-family: "Silkscreen", "Courier New", monospace;
    font-weight: 700;
    color: var(--lavender);
    font-size: 31px;
    line-height: 35px;
    letter-spacing: 1px;
  }
  .masthead__title {
    font-family: "Oswald", "Arial Narrow", sans-serif;
    font-weight: 500;
    color: var(--flame);
    font-size: 58px;
    line-height: 64px;
    margin-top: 6px;
    letter-spacing: 0.5px;
  }
  .quote { position: absolute; font-size: 14.6px; line-height: 21.7px; }
  .quote p { text-align: justify; }
  .quote__by { text-align: right; margin-top: 7px; font-size: 13.2px; line-height: 18px; }
  .quote__name { color: var(--flame); font-weight: 500; display: block; }
  .quote--left { left: 102px; top: 242px; width: 289px; }
  .quote--right { left: 433px; top: 254px; width: 285px; }
  .quote--wide { left: 137px; top: 501px; width: 551px; }
  .quote--wide p { text-align: left; }
  .quote--wide .quote__by { margin-top: 2px; margin-right: -4px; }
  .blurb {
    position: absolute; left: 65px; top: 601px; width: 682px; height: 309px;
    border: 1px solid var(--rule);
    background: var(--panel);
    padding: 26px 34px 0;
    text-align: center;
    font-size: 13.8px; line-height: 20.3px; letter-spacing: 0.2px;
  }
  .blurb p + p { margin-top: 20px; }
  .author-photo { position: absolute; left: 109px; top: 938px; width: 169px; height: 189px; display: block; }
  .author { position: absolute; left: 295px; top: 946px; width: 430px; }
  .author__heading {
    font-family: "Oswald", "Arial Narrow", sans-serif; font-weight: 500;
    color: var(--flame); font-size: 24px; line-height: 32px;
  }
  .author__bio { margin-top: 4px; font-size: 14.6px; line-height: 21.8px; text-align: justify; }
</style>
</head>
<body>
  <header class="masthead">
    <div class="masthead__kicker">PRAISE FOR<br>NINE DOORS OUT OF</div>
    <h1 class="masthead__title">THE ENDLESS LEVEL</h1>
  </header>

  <blockquote class="quote quote--left">
    <p>“A must-read for anyone who is addicted to or thinks they may have a problem with digital gaming. This eloquent work will also be useful to academics and clinicians exploring potential solutions. The author recognizes the similarities between gaming addiction and other addictions, and logically applies one of the most effective known solutions for addiction - The Twelve Steps.”</p>
    <footer class="quote__by"><span class="quote__name">- Leon Barrowfield</span>Noted Interventionist and Keynote Speaker</footer>
  </blockquote>

  <blockquote class="quote quote--right">
    <p>“As a high school teacher for 24 years, husband, father, coach, and 12-Step member, I can assure you that this book will transform the life of anyone who is addicted to video games. Well written, easy to understand, and a wonderful book that will provide you with a clear road map to recovery, and this includes teenagers, a group I have been working with in the classroom for decades.”</p>
    <footer class="quote__by"><span class="quote__name">- Dana Whitlock</span>Harbor Vale, CA High School Teacher.</footer>
  </blockquote>

  <blockquote class="quote quote--wide">
    <p>“If you suffer from digital gaming addiction, I strongly encourage you to use this book as your road map to get you back to the real world.”</p>
    <footer class="quote__by"><span class="quote__name">- Curtis Okafor</span>Founder of Feedline Review.</footer>
  </blockquote>

  <section class="blurb">
    <p>A practical path back from compulsive screen play (aka Video Game Addiction) based on the rich and successful tradition of the Twelve Steps.</p>
    <p>Addiction to Digital Gaming is a new and troubling phenomenon that has burst upon an unprepared society with alarming speed. Many people crave the use of Digital Games in a strikingly similar way to any other addict. Digital Games are a complex software and hardware system that have been designed to promote continued and progressive usage. This sophisticated technology clearly feeds on natural addictive tendencies.</p>
    <p>The 12 Steps are one of the most effective methods for treating addiction in human history. Originating with Recovery Quorum in 1939, the 12 Steps have since been used to treat a variety of other addictions, including drugs, sex, gambling, eating disorders, and many others. Now in this groundbreaking work the 12 Steps are applied to the complex and evolving contemporary phenomenon of Digital Gaming Addiction.</p>
  </section>

  <svg class="author-photo" viewBox="0 0 169 189" role="img" aria-label="Portrait photograph of the author, Peter Halvorn">
    <defs>
      <linearGradient id="portraitTone" x1="0" y1="0" x2="0" y2="1">
        <stop offset="0" stop-color="#7d8a5a"/>
        <stop offset="0.55" stop-color="#8a6a55"/>
        <stop offset="1" stop-color="#1e2230"/>
      </linearGradient>
    </defs>
    <rect width="169" height="189" fill="url(#portraitTone)"/>
  </svg>

  <section class="author">
    <h2 class="author__heading">About the Author</h2>
    <p class="author__bio">Peter Halvorn is a Technology Consultant and Writer with many years of professional coding and consulting experience. He also struggled with addiction to drugs and alcohol and is now clean and sober in a Twelve-Step program for over 17 years. This unique combination of 12-Step experience and technology expertise led him to create Nine Doors Out of the Endless Level.</p>
  </section>
</body>
</html>
```